business card - Helicopter Flight Services, Flight School, etc.

We need a business card design for a new helicopter service.

We offer Helicopter Flight Services, Aerial Filming & Photography, Flight School, and Helicopter Tours. In that order.

Summit BladeAir, Inc.
Dennis Tollerby
SummitBladeair@Kestmail.com
626-418-7352

Based at the Brenwick Airport in Van Nuys, CA. The final design should communicate integrity and safety. Pictures or logos at your discretion.

Card back side - surprise me.

```html
<!DOCTYPE html>
<html lang="en">
<head>
<meta charset="utf-8">
<title>Summit BladeAir, Inc. — Business Card</title>
<link rel="stylesheet" href="https://fonts.googleapis.com/css2?family=Noto+Serif:wght@400&family=Open+Sans:wght@400;600&display=swap">
<style>
  :root {
    --page-bg: #e9e6e1;
    --card-white: #f7f7f7;
    --card-shade: #e4e4e4;
    --band-dark: #2b2b2c;
    --band-red: #b3060c;
    --ink: #1a1a1a;
    --ink-soft: #2a2a2a;
    --on-dark: #ffffff;
  }
  * { box-sizing: border-box; margin: 0; padding: 0; }
  html, body { width: 1200px; height: 892px; overflow: hidden; }
  body {
    background: var(--page-bg);
    display: flex;
    flex-direction: column;
    align-items: center;
    justify-content: center;
    gap: 56px;
  }
  .card {
    position: relative;
    width: 600px;
    height: 343px;
    background: radial-gradient(ellipse at 45% 35%, var(--card-white) 0%, var(--card-shade) 100%);
    overflow: hidden;
    box-shadow: 0 6px 18px rgba(0,0,0,0.18);
  }
  .card-art { position: absolute; display: block; }
  .company-name {
    position: absolute;
    font-family: "Noto Serif", Georgia, serif;
    font-weight: 400;
    color: var(--ink);
    white-space: nowrap;
  }
  /* Front */
  .front .card-art { left: 190px; top: 22px; width: 230px; height: 96px; }
  .front .company-name { left: 40px; top: 56px; font-size: 37px; letter-spacing: 0.2px; }
  .front .wave { position: absolute; inset: 0; width: 600px; height: 343px; }
  .contact-block {
    position: absolute;
    inset: 0;
    font-family: "Open Sans", Arial, sans-serif;
    color: var(--on-dark);
  }
  .person-name {
    position: absolute;
    left: 150px; top: 262px;
    font-size: 20px;
  }
  .divider {
    position: absolute;
    left: 328px; top: 222px;
    width: 1px; height: 64px;
    background: var(--on-dark);
  }
  .contact-lines {
    position: absolute;
    left: 342px; top: 214px;
    list-style: none;
    font-size: 14.5px;
    line-height: 22px;
  }
  .contact-lines li { display: flex; align-items: center; gap: 6px; }
  .contact-lines svg { width: 14px; height: 14px; flex: none; }
  .address {
    position: absolute;
    left: 150px; top: 304px;
    font-size: 14.5px;
  }
  /* Back */
  .back .card-art { left: 110px; top: 60px; width: 380px; height: 230px; }
  .back .company-name { left: 0; right: 0; top: 58px; text-align: center; font-size: 36px; }
  .services {
    position: absolute;
    left: 0; right: 0; top: 160px;
    display: flex;
    justify-content: center;
    gap: 44px;
    list-style: none;
    font-family: "Open Sans", Arial, sans-serif;
    font-size: 19px;
    color: var(--ink-soft);
  }
  .services li::before {
    content: "\2735";
    font-size: 12px;
    margin-right: 10px;
    vertical-align: 3px;
  }
</style>
</head>
<body>

  <section class="card front" aria-label="Card front">
    <svg class="card-art" viewBox="0 0 230 96" role="img" aria-label="Faint illustration of an aircraft in flight">
      <defs>
        <linearGradient id="ghostFront" x1="0" y1="0" x2="1" y2="1">
          <stop offset="0" stop-color="#e6e6e6" stop-opacity="0"/>
          <stop offset="0.5" stop-color="#dcdcdc" stop-opacity="0.8"/>
          <stop offset="1" stop-color="#e6e6e6" stop-opacity="0"/>
        </linearGradient>
      </defs>
      <rect width="230" height="96" rx="36" fill="url(#ghostFront)"/>
    </svg>

    <h1 class="company-name">Summit BladeAir, Inc.</h1>

    <svg class="wave" viewBox="0 0 600 343" aria-hidden="true">
      <path d="M0 232 C 200 224, 330 202, 420 172 C 490 148, 540 132, 600 128 L600 343 L0 343 Z" fill="var(--band-red)"/>
      <path d="M0 244 C 200 236, 335 214, 425 184 C 495 160, 545 144, 600 140 L600 343 L0 343 Z" fill="var(--band-dark)"/>
    </svg>

    <div class="contact-block">
      <p class="person-name">Dennis Tollerby</p>
      <span class="divider" aria-hidden="true"></span>
      <ul class="contact-lines">
        <li>
          <svg viewBox="0 0 14 14" aria-hidden="true"><rect width="14" height="14" rx="2" fill="#fff"/><path d="M4 3.2 L5.6 3 L6.4 5 L5.4 5.8 C5.9 7 6.9 8 8.2 8.6 L9 7.6 L11 8.4 L10.8 10 C7 10.2 3.8 7 4 3.2 Z" fill="var(--band-dark)"/></svg>
          626-418-7352
        </li>
        <li>
          <svg viewBox="0 0 14 14" aria-hidden="true"><rect width="14" height="14" rx="2" fill="#fff"/><rect x="3" y="4.5" width="8" height="5.5" fill="none" stroke="var(--band-dark)" stroke-width="1"/><path d="M3 4.5 L7 7.6 L11 4.5" fill="none" stroke="var(--band-dark)" stroke-width="1"/></svg>
          SummitBladeair@Kestmail.com
        </li>
      </ul>
      <p class="address">2740 W. Larkmoor Ave. Ste.A Redfield, CA 91488</p>
    </div>
  </section>

  <section class="card back" aria-label="Card back">
    <svg class="card-art" viewBox="0 0 380 230" role="img" aria-label="Faint illustration of an aircraft sweeping across the card">
      <defs>
        <radialGradient id="ghostBack" cx="0.5" cy="0.55" r="0.55">
          <stop offset="0" stop-color="#d9d9d9" stop-opacity="0.75"/>
          <stop offset="1" stop-color="#e8e8e8" stop-opacity="0"/>
        </radialGradient>
      </defs>
      <rect width="380" height="230" rx="80" fill="url(#ghostBack)"/>
    </svg>

    <h2 class="company-name">Summit BladeAir, Inc.</h2>

    <ul class="services">
      <li>Brenwick Airport</li>
      <li>Tour guide</li>
      <li>Heliport</li>
    </ul>
  </section>

</body>
</html>
```